Brochure 2 fold and Trifold

We need 2 types of brochure (2 fold and Trifold) design for our Brand "VELVET DAWN" Logo (La douceur de Mirelle) is in rose gold color
Target Market(s)
Women ages 17 and up
Industry/Entity Type
Supplement
Font styles to use
Serif
Script
Requirements
Must have
- Rose gold color tone make it look premium, minimalist look

```html
<!DOCTYPE html>
<html lang="en">
<head>
<meta charset="utf-8">
<title>Velvet Dawn – Brochure Cover Spread</title>
<link rel="stylesheet" href="https://fonts.googleapis.com/css2?family=Libre+Baskerville:wght@400;700&family=Cormorant+Garamond:wght@400;500&family=Marcellus&display=swap">
<style>
  :root {
    --backdrop: #2e2e2e;
    --paper: #f1f1f1;
    --ink: #1e1e1e;
    --rose: #e8897c;
    --rose-light: #f2ada2;
    --rose-deep: #de7a6c;
    --silver: #c9c9c9;
    --silver-dark: #9e9e9e;
    --white: #ffffff;
    --box: #e9e9e9;
    --fern: #5c9b34;
    --capsule: #2f8a6a;
  }
  * { box-sizing: border-box; margin: 0; padding: 0; }
  html, body { width: 1200px; height: 824px; overflow: hidden; }
  body {
    background: var(--backdrop);
    display: flex; align-items: center; justify-content: center;
  }
  .spread { display: flex; width: 1060px; height: 740px; box-shadow: 0 20px 40px rgba(0,0,0,.45); }
  .page {
    position: relative; width: 530px; height: 740px;
    background: var(--paper); overflow: hidden;
  }
  .page-back { border-right: 1px solid #d8d8d8; }
  .swoosh { position: absolute; inset: 0; width: 100%; height: 100%; }

  .serif { font-family: "Libre Baskerville", Georgia, serif; }

  /* Back cover */
  .back-kicker {
    position: absolute; top: 70px; left: 0; right: 0; text-align: center;
    font-family: "Libre Baskerville", Georgia, serif; font-weight: 700;
    font-size: 19px; color: var(--ink);
  }
  .back-headline {
    position: absolute; top: 98px; left: 0; right: 0; text-align: center;
    font-family: "Libre Baskerville", Georgia, serif; font-weight: 700;
    font-size: 38px; color: var(--rose); letter-spacing: .5px;
  }
  .capsules-art {
    position: absolute; top: 160px; left: 95px; width: 340px; height: 300px;
    border-radius: 40px;
    background: radial-gradient(ellipse at 55% 40%, #cfe3da 0%, #6fae94 45%, var(--capsule) 75%, rgba(47,138,106,0) 100%);
  }
  .back-product {
    position: absolute; top: 500px; left: 0; right: 0; text-align: center;
    font-family: "Libre Baskerville", Georgia, serif; font-weight: 700;
    font-size: 30px; color: var(--white);
  }
  .back-tagline {
    position: absolute; top: 540px; left: 0; right: 0; text-align: center;
    font-family: "Libre Baskerville", Georgia, serif; font-weight: 700;
    font-size: 19px; color: var(--white);
  }
  .distributor-label {
    position: absolute; top: 586px; left: 50%; transform: translateX(-50%);
    padding: 5px 18px; border-radius: 3px;
    background: linear-gradient(180deg, #f5f5f5, var(--silver));
    font-family: "Libre Baskerville", Georgia, serif; font-size: 12px; color: var(--ink);
  }
  .distributor-box {
    position: absolute; top: 620px; left: 60px; right: 60px; height: 90px;
    background: var(--box); border-radius: 14px;
  }

  /* Front cover */
  .brand {
    position: absolute; top: 52px; left: 0; right: 0; text-align: center;
    font-family: "Cormorant Garamond", Georgia, serif; font-weight: 500;
    font-size: 30px; letter-spacing: 4px; color: var(--ink);
  }
  .front-product {
    position: absolute; top: 102px; left: 0; right: 0; text-align: center;
    font-family: "Libre Baskerville", Georgia, serif; font-weight: 700;
    font-size: 40px; color: var(--rose);
  }
  .botanicals-art {
    position: absolute; top: 175px; left: 90px; width: 370px; height: 250px;
    border-radius: 30px;
    background: linear-gradient(100deg, var(--fern) 0%, #8bbf5e 40%, #e6e6e6 62%, var(--white) 100%);
  }
  .front-sub {
    position: absolute; top: 560px; left: 0; right: 0; text-align: center;
    font-family: "Marcellus", Georgia, serif; font-size: 19px; color: var(--white);
  }
  .front-headline {
    position: absolute; top: 588px; left: 0; right: 0; text-align: center;
    font-family: "Marcellus", Georgia, serif; font-size: 40px; color: var(--white);
    letter-spacing: 1px;
  }
  .front-rule {
    position: absolute; top: 646px; left: 50%; transform: translateX(-50%);
    width: 160px; height: 2px; background: var(--white);
  }
</style>
</head>
<body>
  <main class="spread">
    <section class="page page-back">
      <svg class="swoosh" viewBox="0 0 530 740" preserveAspectRatio="none" aria-hidden="true">
        <defs>
          <linearGradient id="roseBack" x1="0" y1="0" x2="1" y2="1">
            <stop offset="0" stop-color="#f2ada2"/>
            <stop offset="1" stop-color="#e8897c"/>
          </linearGradient>
          <linearGradient id="silverBack" x1="0" y1="0" x2="1" y2="0">
            <stop offset="0" stop-color="#ffffff"/>
            <stop offset=".5" stop-color="#a8a8a8"/>
            <stop offset="1" stop-color="#e0e0e0"/>
          </linearGradient>
        </defs>
        <path d="M0 470 C150 430 350 400 530 410 L530 740 L0 740 Z" fill="url(#silverBack)"/>
        <path d="M0 488 C150 450 350 422 530 430 L530 740 L0 740 Z" fill="url(#roseBack)"/>
      </svg>
      <p class="back-kicker">One of the first Skin &amp; Sun Protection</p>
      <h2 class="back-headline">ALL IN ONE</h2>
      <div class="capsules-art" role="img" aria-label="Illustration of green translucent supplement capsules"></div>
      <h3 class="back-product">VELVET DAWN</h3>
      <p class="back-tagline">Nature’s solution to skin whitening</p>
      <span class="distributor-label">Distributed by:</span>
      <div class="distributor-box"></div>
    </section>

    <section class="page page-front">
      <svg class="swoosh" viewBox="0 0 530 740" preserveAspectRatio="none" aria-hidden="true">
        <defs>
          <linearGradient id="roseFront" x1="0" y1="0" x2="1" y2="1">
            <stop offset="0" stop-color="#e8897c"/>
            <stop offset="1" stop-color="#f2ada2"/>
          </linearGradient>
          <linearGradient id="silverFront" x1="0" y1="0" x2="1" y2="0">
            <stop offset="0" stop-color="#e0e0e0"/>
            <stop offset=".5" stop-color="#a8a8a8"/>
            <stop offset="1" stop-color="#ffffff"/>
          </linearGradient>
        </defs>
        <path d="M0 415 C180 470 380 470 530 380 L530 740 L0 740 Z" fill="url(#silverFront)"/>
        <path d="M0 440 C180 495 380 492 530 405 L530 740 L0 740 Z" fill="url(#roseFront)"/>
      </svg>
      <p class="brand">La douceur de Mirelle</p>
      <h1 class="front-product">VELVET DAWN</h1>
      <div class="botanicals-art" role="img" aria-label="Photograph of a green fern frond beside two white tomatoes"></div>
      <p class="front-sub">Skin Whitening &amp; Sun Protection all in one</p>
      <h2 class="front-headline">ORAL SUPPLEMENTS</h2>
      <span class="front-rule"></span>
    </section>
  </main>
</body>
</html>
```